Expedition Cruise Sales Website for the Polar Regions (Antarctica & Arctic)

This will be a website for selling cruises.
This site should have a homepage, a ship page, destinations, and itineraries.
I have created a file specifying each page, and it is attached.
Pages:
1. Home
2. Cruise Lines
- 2.1 Ships
3. Destinations
- 3.1 Region - 3.2 Country - 3.3 City
4. Itineraries
- 4.1 Itinerary
5. Blog / Travel Tips 6. About Us
7. Contact
Please take a look on the attached pdf
Target Market(s)
Expedition Travelers
Coding
Coded - Design and coding required
Number of Pages Required
5+ page
Font styles to use
Look and feel
Each slider illustrates characteristics of the customer's brand and the style your logo design should communicate.

```html
<!DOCTYPE html>
<html lang="en">
<head>
<meta charset="utf-8">
<title>Boreala.co — Polar Expedition Cruises</title>
<link href="https://fonts.googleapis.com/css2?family=Plus+Jakarta+Sans:wght@400;500;600;700&family=Figtree:ital,wght@0,400;0,500;0,600;1,400&display=swap" rel="stylesheet">
<style>
:root{
  --blue:#2f6db3;
  --blue-dark:#245a98;
  --navy:#0f1f3d;
  --ink:#1c2230;
  --muted:#6b7280;
  --orange:#e8900c;
  --ice:#d2e1f2;
  --field:#f3f6fb;
  --line:#d9dee6;
  --white:#ffffff;
}
*{box-sizing:border-box;margin:0;padding:0}
html,body{width:1200px;height:3766px;overflow:hidden;background:var(--white)}
body{font-family:"Figtree",sans-serif;color:var(--ink)}
.page{position:relative;width:1200px;height:3766px;overflow:hidden}
.abs{position:absolute}
h1,h2,h3,.brand,.btn{font-family:"Plus Jakarta Sans",sans-serif}
.btn{position:absolute;display:flex;align-items:center;justify-content:center;background:var(--blue);color:var(--white);border-radius:24px;font-weight:700;font-size:15px;letter-spacing:.2px;text-transform:uppercase}
.btn.dark{background:var(--navy)}

/* header */
.brand{position:absolute;font-weight:700;color:var(--blue);font-size:25px}
.contact{position:absolute;top:18px;left:540px;display:flex;align-items:center;gap:14px;font-size:13px;color:#4b5563}
.contact .sep{width:1px;height:18px;background:var(--line)}
.social{display:flex;gap:8px}
.social span{width:24px;height:24px;border-radius:50%;border:1px solid var(--line);display:block;background:#f6f8fb}
.nav{position:absolute;top:66px;left:331px;display:flex;gap:36px;font-size:14px;font-weight:500;text-transform:uppercase;color:var(--ink)}
.nav .active{color:var(--blue)}

/* hero */
.hero{position:absolute;top:102px;left:0;width:1200px;height:565px;background:linear-gradient(180deg,#8fb6dd 0%,#bfd6ec 18%,#3f78b4 36%,#1f4f86 60%,#16406f 100%)}
.hero h1{position:absolute;top:242px;left:142px;color:var(--white);font-size:46px;font-weight:700}
.hero p{position:absolute;top:314px;left:142px;color:var(--white);font-size:17.5px;line-height:28px}

/* book */
.section-title{position:absolute;left:0;width:1200px;text-align:center;font-size:38px;font-weight:600;color:var(--ink)}
.field-label{position:absolute;font-size:12px;color:var(--ink)}
.field{position:absolute;height:41px;background:var(--field);border:1px solid var(--line);border-radius:4px;font-size:11px;color:#9aa3ae;padding:13px 13px}

/* offers */
.offer{position:absolute;top:979px;width:288px;height:420px;background:var(--white);box-shadow:0 2px 12px rgba(20,40,80,.12)}
.offer.focus{border:1px solid #9cc0ea}
.offer h3{position:absolute;top:21px;left:25px;font-size:17px;font-weight:500;color:var(--ink)}
.offer .price{position:absolute;top:52px;left:25px;font-size:18px;color:var(--orange);font-weight:500}
.offer p{position:absolute;top:84px;left:25px;width:245px;font-size:13.5px;line-height:23px;color:var(--muted)}
.offer .btn{top:149px;left:25px;width:129px;height:44px;font-size:14px}
.offer .photo{position:absolute;left:7px;top:212px;width:274px;height:200px}
.arrow{position:absolute;width:36px;height:36px;border-radius:50%;display:flex;align-items:center;justify-content:center}

/* destinations */
.dest-title{position:absolute;top:1646px;left:647px;color:var(--white);font-size:38px;font-weight:600}
.dest-sub{position:absolute;top:1705px;left:647px;color:var(--white);font-size:19px}
.dest-text{position:absolute;top:1746px;left:647px;width:420px;color:var(--white);font-size:13.6px;line-height:25.6px}
.dots{position:absolute;top:1982px;left:649px;display:flex;gap:6px}
.dots span{width:16px;height:4px;border-radius:2px;background:#cfe0f4}
.dots span:first-child{width:24px;background:var(--navy)}

/* highlights */
.lead{position:absolute;left:150px;width:900px;text-align:center;font-size:18px;line-height:28px;color:var(--ink)}
.small{position:absolute;left:145px;width:910px;text-align:center;font-size:13px;line-height:24px;color:var(--muted)}

/* testimonials */
.review{position:absolute;top:2619px;width:319px;height:253px;background:var(--white);border-radius:12px;box-shadow:0 2px 12px rgba(20,40,80,.12);padding:22px 25px}
.stars{color:#f5b400;font-size:15px;letter-spacing:2px}
.review h3{font-size:15px;font-weight:500;margin-top:8px;color:var(--ink)}
.review p{margin-top:10px;font-size:13px;line-height:21px;color:var(--muted)}
.who{position:absolute;left:25px;bottom:22px;display:flex;align-items:center;gap:14px}
.avatar{width:56px;height:56px;border-radius:50%;background:linear-gradient(135deg,#c9d6e6,#8aa4c2)}
.who b{display:block;color:var(--blue);font-weight:500;font-size:13px;text-transform:uppercase}
.who small{display:block;font-size:12px;color:var(--ink);margin-top:6px}

/* newsletter */
.pill{position:absolute;top:3249px;height:44px;background:var(--white);border-radius:22px;font-size:11px;color:#9aa3ae;padding:15px 20px}

/* footer */
.fnav{position:absolute;top:3597px;left:0;width:1200px;display:flex;justify-content:center;gap:18px;font-size:14px;color:var(--ink);text-transform:uppercase}
.fnav i{font-style:normal}
.legal{position:absolute;top:3665px;left:0;width:1200px;text-align:center;font-size:12px;color:var(--ink)}
</style>
</head>
<body>
<div class="page">

<!-- header -->
<div class="abs" style="top:18px;left:177px;width:44px;height:40px;border-radius:50%;background:var(--blue)"></div>
<div class="brand" style="top:62px;left:143px">Boreala.co</div>
<div class="contact">
  <span>✉ hello@boreala-voyages.com</span><span class="sep"></span>
  <span>☏ +1-800-555-0142</span><span class="sep"></span>
  <div class="social"><span></span><span></span><span></span><span></span></div>
</div>
<nav class="nav">
  <span class="active">Home</span><span>Cruise</span><span>Lines</span><span>Destinations</span><span>Itineraries</span><span>Blog</span><span>About Us</span><span>Contact</span>
</nav>

<!-- hero -->
<section class="hero" role="img" aria-label="Cruise ship sailing on deep blue sea under a bright cloudy sky">
  <h1 style="top:140px">Welcome To Boreala.co</h1>
  <p style="top:212px">Lorem ipsum dolor sit amet, consectetur adipiscing elit,<br>sed do eiusmod tempor incididunt ut labore</p>
  <div class="btn" style="top:300px;left:142px;width:150px;height:44px">Get Started</div>
</section>
<svg class="abs" style="top:530px;left:0" width="1200" height="140" viewBox="0 0 1200 140">
  <path d="M0,138 Q600,-10 1200,138 L1200,140 L0,140 Z" fill="var(--white)"/>
  <path d="M0,138 Q600,-10 1200,138 L1200,128 Q600,-22 0,128 Z" fill="var(--blue)"/>
</svg>

<!-- book now -->
<h2 class="section-title" style="top:664px">Book Now</h2>
<div class="field-label" style="top:755px;left:186px">Cruising to</div>
<div class="field-label" style="top:755px;left:409px">Leaving from</div>
<div class="field-label" style="top:755px;left:620px">Leaving On</div>
<div class="field" style="top:779px;left:186px;width:200px">Any Where</div>
<div class="field" style="top:779px;left:409px;width:200px">Any Port</div>
<div class="field" style="top:779px;left:620px;width:200px">Any Date</div>
<div class="btn" style="top:779px;left:843px;width:170px;height:41px;font-size:14px">Search Cruises
  <svg width="14" height="14" viewBox="0 0 14 14" style="margin-left:6px"><circle cx="6" cy="6" r="4.5" fill="none" stroke="#fff" stroke-width="2"/><path d="M9.5 9.5L13 13" stroke="#fff" stroke-width="2"/></svg></div>

<!-- featured offers -->
<h2 class="section-title" style="top:892px">Featured Offers</h2>
<div class="arrow" style="top:1170px;left:96px;background:#e8eef7"><svg width="12" height="12" viewBox="0 0 12 12"><path d="M8 1L3 6l5 5" fill="none" stroke="var(--navy)" stroke-width="2"/></svg></div>
<div class="arrow" style="top:1170px;left:1068px;background:var(--navy)"><svg width="12" height="12" viewBox="0 0 12 12"><path d="M4 1l5 5-5 5" fill="none" stroke="#fff" stroke-width="2"/></svg></div>

<article class="offer" style="left:143px">
  <h3>Lorem ipsum dolor</h3><div class="price">$75.00</div>
  <p>Duis aute irure dolor in reprehenderit in voluptate velit esse cillum dolore</p>
  <div class="btn">Learn More</div>
  <div class="photo" role="img" aria-label="Travellers on a ship deck pointing at the sky" style="background:linear-gradient(180deg,#a9cdea,#d8c3a8)"></div>
</article>
<article class="offer focus" style="left:457px">
  <h3>Lorem ipsum dolor</h3><div class="price">$75.00</div>
  <p>Duis aute irure dolor in reprehenderit in voluptate velit esse cillum dolore</p>
  <div class="btn">Learn More</div>
  <div class="photo" role="img" aria-label="Two cruise ships docked at a pier with passengers walking" style="background:linear-gradient(180deg,#c7dcef,#5f7f9a)"></div>
</article>
<article class="offer" style="left:769px">
  <h3>Lorem ipsum dolor</h3><div class="price">$75.00</div>
  <p>Duis aute irure dolor in reprehenderit in voluptate velit esse cillum dolore</p>
  <div class="btn">Learn More</div>
  <div class="photo" role="img" aria-label="Traveller reading a map beside a cruise ship" style="background:linear-gradient(180deg,#8fa7bf,#e7e3dc)"></div>
</article>

<!-- destinations -->
<svg class="abs" style="top:1490px;left:0" width="1200" height="640" viewBox="0 0 1200 640">
  <path d="M0,18 Q600,140 1200,18 L1200,622 Q600,480 0,622 Z" fill="var(--blue)"/>
  <path d="M140,40 Q600,120 1060,40 Q600,98 140,40 Z" fill="var(--navy)"/>
  <path d="M60,612 Q600,490 1140,612 Q600,510 60,612 Z" fill="var(--navy)"/>
</svg>
<div class="abs" role="img" aria-label="Aerial view of a harbour city with marina and skyline" style="top:1605px;left:143px;width:418px;height:418px;border-radius:50%;background:radial-gradient(circle at 50% 40%,#9fb4c4,#2e6b8f 70%,#5c6b72)"></div>
<h2 class="dest-title">Destinations</h2>
<div class="dest-sub">Country</div>
<p class="dest-text">Duis aute irure dolor in reprehenderit in voluptate velit esse cillum dolore eu fugiat nulla pariatur. Excepteur sint occaecat cupidatat non proident, sunt in culpa qui officia deserunt<br>Nemo enim ipsam voluptatem quia voluptas sit aspernatur aut odit aut fugit, sed quia consequuntur magni dolores eos qui ratione</p>
<div class="btn dark" style="top:1904px;left:649px;width:131px;height:43px;text-transform:none;font-weight:600">LEARN MORE</div>
<div class="dots"><span></span><span></span><span></span></div>

<!-- highlights -->
<h2 class="section-title" style="top:2132px">Cruise Line Highlights</h2>
<p class="lead" style="top:2194px">Lorem ipsum dolor sit amet, consectetur adipiscing elit, sed do eiusmod tempor incididunt ut labore et dolore magna aliqua. Ut enim ad minim veniam, quis nostrud exercitation ullamco laboris</p>
<p class="small" style="top:2258px">Duis aute irure dolor in reprehenderit in voluptate velit esse cillum dolore eu fugiat nulla pariatur. Excepteur sint occaecat cupidatat non proident, sunt in culpa qui officia deserunt mollit anim id est laborum.Sed ut perspiciatis unde omnis iste natus error sit voluptatem accusantium doloremque laudantium, totam rem aperiam eaque ipsa quae ab illo inventore veritatis et quasi architecto beatae vitae dicta sunt explic</p>
<p class="small" style="top:2340px;font-style:italic;color:var(--ink);font-size:14px">Nemo enim ipsam voluptatem quia</p>
<div class="btn" style="top:2398px;left:535px;width:130px;height:43px;font-size:14px">Learn More</div>

<!-- testimonials -->
<h2 class="abs" style="top:2510px;left:143px;font-size:35px;font-weight:600">Customer Testimonials</h2>
<div class="abs" style="top:2570px;left:143px;font-size:15px;color:var(--blue)">800+ Verified Customer Reviews</div>
<div class="arrow" style="top:2567px;left:990px;width:26px;height:26px;background:#8a8f96"><svg width="10" height="10" viewBox="0 0 12 12"><path d="M8 1L3 6l5 5" fill="none" stroke="#fff" stroke-width="2"/></svg></div>
<div class="arrow" style="top:2567px;left:1027px;width:26px;height:26px;background:var(--navy)"><svg width="10" height="10" viewBox="0 0 12 12"><path d="M4 1l5 5-5 5" fill="none" stroke="#fff" stroke-width="2"/></svg></div>

<article class="review" style="left:143px">
  <div class="stars">★★★★★</div><h3>HIGHLY RECOMMEND</h3>
  <p>Sed ut perspiciatis unde omnis iste natus error sit voluptatem accusantium doloremque laudantium, totam rem aperiam, eaque ipsa quae ab illo inventore veritatis et</p>
  <div class="who"><div class="avatar" role="img" aria-label="Reviewer portrait"></div><div><b>Nora Bell</b><small>▦ 10.11.2024</small></div></div>
</article>
<article class="review" style="left:479px">
  <div class="stars">★★★★★</div><h3>HIGHLY RECOMMEND</h3>
  <p>Sed ut perspiciatis unde omnis iste natus error sit voluptatem accusantium doloremque laudantium, totam rem aperiam, eaque ipsa quae ab illo inventore veritatis et</p>
  <div class="who"><div class="avatar" role="img" aria-label="Reviewer portrait"></div><div><b>Lena Ortiz</b><small>▦ 10.07.2024</small></div></div>
</article>
<article class="review" style="left:815px">
  <div class="stars">★★★★★</div><h3>HIGHLY RECOMMEND</h3>
  <p>Sed ut perspiciatis unde omnis iste natus error sit voluptatem accusantium doloremque laudantium, totam rem aperiam, eaque ipsa quae ab illo inventore veritatis et</p>
  <div class="who"><div class="avatar" role="img" aria-label="Reviewer portrait"></div><div><b>Owen Marsh</b><small>▦ 08.21.2024</small></div></div>
</article>
<article class="review" style="left:1155px">
  <div class="stars">★★★★★</div><h3>HIGHLY RECOMMEND</h3>
  <p>Sed ut perspiciatis unde omnis iste natus error sit voluptatem accusantium doloremque laudantium</p>
</article>
<div class="btn" style="top:2917px;left:143px;width:181px;height:43px;font-size:14px">View More Reviews</div>

<!-- newsletter -->
<svg class="abs" style="top:2995px;left:0" width="1200" height="445" viewBox="0 0 1200 445">
  <path d="M0,13 Q600,110 1200,13 L1200,440 Q600,320 0,440 Z" fill="var(--ice)"/>
  <path d="M140,70 Q600,150 1060,70 Q600,128 140,70 Z" fill="var(--blue)"/>
  <path d="M60,430 Q600,310 1140,430 Q600,330 60,430 Z" fill="var(--blue)"/>
</svg>
<h2 class="section-title" style="top:3128px;font-size:39px">Subscribe To Join Our Newsletter</h2>
<p class="abs" style="top:3200px;left:0;width:1200px;text-align:center;font-size:13px">Lorem ipsum dolor sit amet, consectetur adipiscing elit, sed do eiusmod tempo</p>
<div class="pill" style="left:243px;width:279px">First Name</div>
<div class="pill" style="left:535px;width:278px">Email Address</div>
<div class="btn" style="top:3249px;left:821px;width:135px;height:44px;font-size:16px">Subscribe</div>

<!-- footer -->
<div class="abs" style="top:3496px;left:577px;width:46px;height:40px;border-radius:50%;background:var(--blue)"></div>
<div class="brand" style="top:3535px;left:0;width:1200px;text-align:center;font-size:35px">Boreala.co</div>
<nav class="fnav"><span>Home</span><i>|</i><span>Cruise</span><i>|</i><span>Lines</span><i>|</i><span>Destinations</span><i>|</i><span>Itineraries</span><i>|</i><span>Blog</span><i>|</i><span>About Us</span><i>|</i><span>Contact</span></nav>
<div class="abs" style="top:3642px;left:143px;width:914px;height:1px;background:var(--line)"></div>
<div class="legal">© 2025 Boreala.co - All Rights Reserved &nbsp;|&nbsp; FAQ &nbsp;|&nbsp; Privacy Policy &nbsp;|&nbsp; Term of Services</div>
<div class="abs social" style="top:3708px;left:535px;gap:10px">
  <span style="width:26px;height:26px"></span><span style="width:26px;height:26px"></span><span style="width:26px;height:26px;background:var(--blue);border-color:var(--blue)"></span><span style="width:26px;height:26px"></span>
</div>

</div>
</body>
</html>
```